Appraisal and Umpire Services for Property Damage Insurance Claims

I need a banner design that I can post as an advertisement on industry web pages. I would like this to be elegant and reflective of quality, integrity and professionalism.

Target Market(s)

Insurance Companies and Attorneys

Industry/Entity Type

Insurance

Contact Information for Business Card

Gordon T. Ashby
218 Birchwell Lane
PO Box 913
Clifton Park, NY 12348
gashby@meridaleclaims.com
Phone: (800) 519-4867, Ext. 2716
Direct: (315) 648-9052

Logo Text

Line One: Silver Hollow Claim Service, Inc. Line two: Appraisal and Umpire Services

Font styles to use
Serif
Sans Serif

Colors
0255a3
f78f20
faa54b
3176b5

Requirements
Must have
• New Logo and matching banner, business card and stationary.
• The colors must be orange and navy blue in the logo. I have selected them below.

```html
<!DOCTYPE html>
<html lang="en">
<head>
<meta charset="utf-8">
<title>Silver Hollow Claim Service – Appraisal and Umpire Services Banner</title>
<link rel="stylesheet" href="https://fonts.googleapis.com/css2?family=Raleway:wght@300;400;800&family=Source+Sans+3:wght@400;700&display=swap">
<style>
  :root {
    --navy: #0255a3;
    --orange: #f78f20;
    --orange-deep: #ff6a00;
    --white: #ffffff;
    --backdrop: #000000;
  }
  html, body {
    margin: 0;
    width: 1200px;
    height: 1200px;
    overflow: hidden;
    background: var(--backdrop);
  }
  .banner {
    position: absolute;
    left: 111px;
    top: 498px;
    width: 978px;
    height: 204px;
    background: var(--navy);
    overflow: hidden;
    color: var(--white);
  }
  .banner-shapes {
    position: absolute;
    inset: 0;
  }
  .brand {
    position: absolute;
    left: 34px;
    top: 17px;
    display: flex;
    align-items: center;
  }
  .brand-mark {
    width: 40px;
    height: 40px;
    border-radius: 50%;
    background: var(--orange-deep);
    margin-right: 10px;
  }
  .brand-text {
    position: relative;
  }
  .brand-name {
    font-family: "Raleway", sans-serif;
    font-weight: 300;
    font-size: 29px;
    line-height: 1;
    letter-spacing: -0.2px;
  }
  .brand-sub {
    position: absolute;
    right: 34px;
    top: 28px;
    font-family: "Raleway", sans-serif;
    font-weight: 400;
    font-size: 8px;
    white-space: nowrap;
  }
  .headline {
    position: absolute;
    left: 34px;
    top: 84px;
    margin: 0;
    font-family: "Raleway", sans-serif;
    font-weight: 800;
    font-size: 26px;
    line-height: 22px;
    letter-spacing: -0.2px;
  }
  .contact {
    position: absolute;
    left: 34px;
    top: 147px;
    margin: 0;
    font-family: "Source Sans 3", sans-serif;
    font-weight: 400;
    font-size: 16px;
    line-height: 21px;
    letter-spacing: -0.2px;
  }
  .contact strong { font-weight: 700; }
</style>
</head>
<body>
  <section class="banner">
    <svg class="banner-shapes" viewBox="0 0 978 204" width="978" height="204">
      <defs>
        <linearGradient id="office-tones" x1="0" y1="0" x2="0" y2="1">
          <stop offset="0" stop-color="#dfe9f1"/>
          <stop offset="0.45" stop-color="#b9d0e4"/>
          <stop offset="0.7" stop-color="#5a3f33"/>
          <stop offset="1" stop-color="#2e201a"/>
        </linearGradient>
      </defs>
      <polygon class="accent-band" points="424,0 978,0 978,204 905,204 350,129" fill="var(--orange-deep)"/>
      <polygon class="photo-area" points="446,0 978,0 978,199 362,127" fill="url(#office-tones)"
               role="img" aria-label="Photo of a professional in a shirt and tie signing a document at a desk"/>
    </svg>

    <div class="brand">
      <div class="brand-mark"></div>
      <div class="brand-text">
        <div class="brand-name">Silver Hollow</div>
        <div class="brand-sub">Claim Service, Inc</div>
      </div>
    </div>

    <h1 class="headline">Appraisal and Umpire<br>Services</h1>

    <p class="contact">
      <strong>Contact:</strong> Gordon T. Ashby,<br>
      <strong>Email:</strong> gashby@meridaleclaims.com, <strong>Phone:</strong> (800) 519-4867, Ext. 2716
    </p>
  </section>
</body>
</html>
```